Tech Savy small Business accountant business card design

We need a business card for a new company based in the cloud. We provide tax, business advisory, accounting, information technology solutions and back office functions to small businesses. We offer fixed fee packages with add on services as you need them. By harnessing technology we simplify small business operational processes providing valuable time and information for small business owners to grow their business. In the logo (bluvoria) we want to be able to see bluv and experts. The final design should communicate achieving growth dreams and balance (ie life and $).
Updates
This project has been temporarily placed on hold until I finalize "Tech Savy small Business accountant needs a logo". I invite all designers to submit on this logo project. Once my logo is finalized I will resume this business card contest. Thanks Added Wednesday, March 19, 2014
This project has been temporarily placed on hold until I finalize "Tech Savy small Business accountant logo". I invite all designers to submit on this logo project. Once my logo is finalized I will resume this business card contest. Thanks Added Thursday, March 20, 2014
Target Market(s)
Small Business (Revenue $500,000, more than 3 employees) owners.
Industry/Entity Type
Small Business
Contact Information for Business Card
Marcy Elwind (Principal)
Accountant, Tax Agent.
TEL | 0417 683 912
EMAIL | Marcy.Elwind@bluvoria.com.au
WEB | www.bluvoria.com.au
Look and feel

```html
<!DOCTYPE html>
<html lang="en">
<head>
<meta charset="utf-8">
<title>bluvoria business card</title>
<link rel="stylesheet" href="https://fonts.googleapis.com/css2?family=Open+Sans:wght@300;400;700&display=swap">
<style>
  :root {
    --stage: #e9e7e3;
    --card-white: #f7f7f7;
    --slate: #6f7075;
    --slate-dark: #5d5e63;
    --sky: #1fa6d3;
    --ink: #555659;
    --paper-text: #f2f2f2;
    --muted-text: #d9d9dc;
  }
  * { box-sizing: border-box; margin: 0; padding: 0; }
  html, body { width: 1200px; height: 780px; overflow: hidden; }
  body {
    background: var(--stage);
    font-family: "Open Sans", Arial, sans-serif;
    display: flex;
    align-items: center;
    justify-content: center;
    gap: 40px;
  }
  .card {
    position: relative;
    width: 540px;
    height: 330px;
    border-radius: 4px;
    overflow: hidden;
    box-shadow: 0 8px 22px rgba(0,0,0,0.22);
  }
  .card-front { background: var(--card-white); }
  .front-backdrop { position: absolute; inset: 0; }
  .brand { position: absolute; left: 36px; top: 42px; }
  .brand-name {
    font-weight: 700;
    font-size: 56px;
    letter-spacing: -2px;
    color: var(--ink);
    line-height: 1;
  }
  .brand-tagline {
    font-weight: 400;
    font-size: 13.5px;
    color: var(--ink);
    margin-top: 6px;
    letter-spacing: 0.2px;
  }
  .contact {
    position: absolute;
    left: 296px;
    top: 168px;
    color: var(--paper-text);
  }
  .contact-name { font-weight: 300; font-size: 22px; line-height: 1.1; white-space: nowrap; }
  .contact-role-note { font-size: 12px; }
  .contact-title { font-size: 12px; font-weight: 400; color: var(--muted-text); margin-bottom: 12px; }
  .contact-line {
    display: flex;
    align-items: center;
    gap: 8px;
    font-size: 12px;
    line-height: 1.7;
    white-space: nowrap;
  }
  .contact-icon { width: 13px; height: 13px; flex: none; }
  .web {
    position: absolute;
    right: 22px;
    bottom: 18px;
    font-size: 12px;
    color: var(--paper-text);
  }
  .card-back {
    background: linear-gradient(135deg, var(--slate) 0%, var(--slate-dark) 100%);
    display: flex;
    flex-direction: column;
    align-items: center;
    justify-content: center;
    color: var(--paper-text);
  }
  .card-back .brand-name { color: var(--paper-text); font-size: 72px; }
  .card-back .brand-tagline { color: var(--paper-text); font-size: 17px; margin-top: 10px; }
</style>
</head>
<body>
  <section class="card card-front">
    <svg class="front-backdrop" width="540" height="330" viewBox="0 0 540 330" aria-hidden="true">
      <path d="M430 0 C400 110 300 130 250 170 C200 215 175 280 165 330 L540 330 L540 0 Z" fill="var(--sky)"/>
      <path d="M458 0 C428 110 328 130 278 170 C228 215 203 280 193 330 L540 330 L540 0 Z" fill="var(--slate)"/>
    </svg>
    <div class="brand">
      <div class="brand-name">bluvoria</div>
      <div class="brand-tagline">Your business and accounting partner</div>
    </div>
    <div class="contact">
      <div class="contact-name">Marcy Elwind <span class="contact-role-note">(Principal)</span></div>
      <div class="contact-title">Accountant, Tax Agent</div>
      <div class="contact-line">
        <svg class="contact-icon" viewBox="0 0 14 14" aria-hidden="true"><rect x="0.5" y="0.5" width="13" height="13" fill="none" stroke="currentColor"/><path d="M4 3 L6 3 L6.5 5.5 L5.5 6.3 Q6.5 8 8 8.5 L8.8 7.5 L11 8 L11 10 Q7 11 3.5 6 Q3 4 4 3Z" fill="currentColor"/></svg>
        <span>0417 683 912</span>
      </div>
      <div class="contact-line">
        <svg class="contact-icon" viewBox="0 0 14 14" aria-hidden="true"><rect x="0.5" y="0.5" width="13" height="13" fill="none" stroke="currentColor"/><rect x="3" y="4" width="8" height="6" fill="none" stroke="currentColor"/><path d="M3 4 L7 7.5 L11 4" fill="none" stroke="currentColor"/></svg>
        <span>Marcy.Elwind@bluvoria.com.au</span>
      </div>
    </div>
    <div class="web">www.bluvoria.com.au</div>
  </section>

  <section class="card card-back">
    <div class="brand-name">bluvoria</div>
    <div class="brand-tagline">Your business and accounting partner</div>
  </section>
</body>
</html>
```